The Velvet Easel Co - Photos to Custom Oil Paintings

We need a website and logo designed and built allowing customers to purchase custom oil paintings. The paintings will come from a customers single photograph or even combination of photos. They will be able to complete a straight forward checkout process, selecting their desired medium (oil or charcoal painting), their desired size, the number of figures in the painting, the type of background required (as per photo or let the artist decide). Which will then automaticaly provide the customer with a price for the purchase. Allowing them to add a photo to the order which they can then submit with the order present in their personal account etc etc etc.
Theres one website in particular that i will be competing with. That is based in the US - http://www.brushmorrow.com
I wish to far exceed the appearence of the already present site.
At the moment i wish to include Coinvale in the payment process. Unless there are some cheaper, more cost efficient ways, please let me know.
The company name is The Velvet Easel Co. Domain has been purchased - www.thevelveteasel.co (via Hostlark - Linux)
I have no great sense of design, but the site must be straight forward, eye catching, engaging and give the customer a sense of high quality. Some kind of flash animation with pictures on the front page scrolling?
For myself, the admin side, ideally must be straight forward to maintain. The ability to update customers accounts with info (they will then be informed there is an update in their account etc)
The ability for automated emails from point of sale (sales orders with generated order numbers) to myself. Again automated emails to the customers once the "status" of their order or other information has been submitted to their account (by myself) or a similar system.
Updates
All,
Please note, the budget is able to increase subject to what additional work is needed. As far as the admin area goes. I am open to suggestions to ensure ease of use and efficiency.
Any questions, comments or ideas are fully welcomed.
Many thanks,
Dan Holloway
Industry/Entity Type
It Company
Logo Text
Logo styles of interest
Pictorial/Combination Logo
Abstract Logo
Wordmark Logo
Lettermark Logo
Look and feel
Each slider illustrates characteristics of the customer's brand and the style your logo design should communicate.

```html
<!DOCTYPE html>
<html lang="en">
<head>
<meta charset="utf-8">
<title>The Velvet Easel Co – Photos to Custom Oil Paintings</title>
<link rel="stylesheet" href="https://fonts.googleapis.com/css2?family=Arimo:wght@400;700&family=Ubuntu:wght@400;500&display=swap">
<style>
:root{
  --cyan:#1fc5dc;
  --cyan-light:#5fdcef;
  --cyan-dark:#17b3cc;
  --teal-text:#1b9cbc;
  --ink:#1a1a1a;
  --muted:#666;
  --nav-bg:#e1e4e7;
  --panel-line:#d9dcdf;
  --grey-box:#ebedef;
  --gold:#f0b92a;
  --gold-dark:#d9961a;
  --brown:#5a3a0c;
  --logo-red:#e2411d;
  --orange:#f26a1b;
}
*{box-sizing:border-box;margin:0;padding:0}
html,body{width:1036px;height:1200px;overflow:hidden}
body{
  position:relative;
  font-family:"Arimo",Arial,sans-serif;
  color:var(--ink);
  background:
    radial-gradient(ellipse 120px 260px at 20px 250px,rgba(240,70,150,.45),transparent 70%),
    radial-gradient(ellipse 160px 220px at 40px 90px,rgba(255,220,90,.55),transparent 70%),
    radial-gradient(ellipse 140px 300px at 10px 1000px,rgba(245,120,170,.4),transparent 70%),
    radial-gradient(ellipse 200px 160px at 640px 40px,rgba(90,210,230,.35),transparent 70%),
    radial-gradient(ellipse 220px 300px at 1000px 700px,rgba(120,215,235,.25),transparent 70%),
    radial-gradient(ellipse 260px 200px at 700px 1180px,rgba(255,225,120,.35),transparent 70%),
    #fbfcfd;
}
.abs{position:absolute}

/* header */
.logo{left:80px;top:24px;display:flex;align-items:center;gap:8px}
.logo-mark{width:36px;height:50px;border-radius:4px;background:linear-gradient(160deg,#f7d7a0,#c9874a)}
.logo-name{font-family:"Ubuntu",sans-serif;font-size:25px;font-weight:400;color:var(--logo-red);letter-spacing:.2px}
.account-links{left:860px;top:8px;font-size:11px;color:#222}
.account-links span{margin:0 4px}
.order-cta{left:737px;top:30px;width:201px;height:45px;border-radius:22px;
  background:linear-gradient(#f8d25a,var(--gold) 55%,var(--gold-dark));
  border:2px solid #fff;box-shadow:0 1px 3px rgba(0,0,0,.3);
  font-family:"Ubuntu",sans-serif;font-weight:500;font-size:13px;line-height:16px;color:var(--brown);
  text-align:center;padding-top:5px}
.order-cta svg{position:absolute;left:60px;top:41px}

/* navigation */
.main-nav{left:82px;top:100px;width:876px;height:35px;background:var(--nav-bg);border-radius:3px;
  display:flex;align-items:center;padding-left:14px;font-size:12px;color:var(--muted)}
.main-nav a{color:inherit;text-decoration:none;margin-right:0}
.nav-item{padding:6px 7px}
.nav-item.is-active{background:linear-gradient(var(--cyan-light),var(--cyan-dark));color:#0d5b6b;border-radius:3px;border:1px solid #129db4}

/* content panel */
.content-panel{left:82px;top:143px;width:876px;height:800px;background:#fff;border:1px solid var(--panel-line);border-radius:3px;box-shadow:0 1px 4px rgba(0,0,0,.08)}
.slider-frame{left:106px;top:147px;width:822px;height:281px;border-radius:10px;
  background:linear-gradient(#f4f5f6,#c9cdd1);box-shadow:0 6px 8px -4px rgba(0,0,0,.3)}
.slide-before{left:120px;top:157px;width:384px;height:255px;background:linear-gradient(120deg,#1c1b1d,#6e5346 45%,#c99a83 60%,#201f21)}
.slide-after{left:504px;top:157px;width:411px;height:255px;background:linear-gradient(240deg,#3b3a48,#7a6458 40%,#e0b190 60%,#3c3b47)}
.slide-strip{left:403px;top:382px;width:208px;height:30px;background:#fff;display:flex;gap:4px;padding:2px 3px}
.slide-strip i{flex:1;background:linear-gradient(#b58d78,#4a3a34)}
.slider-arrow{top:255px;width:37px;height:37px;border-radius:50%;background:radial-gradient(#fdfdfd,#c6cacd);border:2px solid #fff;box-shadow:0 1px 3px rgba(0,0,0,.3)}
.slider-arrow svg{display:block;margin:9px auto}

.thumb-row{left:92px;top:437px;width:854px;height:136px;background:var(--grey-box);border-radius:3px}
.thumb{top:450px;width:123px;height:111px;border-bottom:3px solid}

/* sections */
.section-head{height:29px;border-radius:3px;background:linear-gradient(var(--cyan-light),var(--cyan-dark));
  color:#fff;font-family:"Ubuntu",sans-serif;font-size:14px;padding:6px 12px;letter-spacing:.3px}
.features{left:92px;top:630px;width:585px}
.feature h3{font-size:12px;font-weight:700;color:var(--teal-text);margin-bottom:2px}
.feature p{font-size:11px;line-height:12.5px}
.testimonials{left:699px;top:620px;width:247px;height:289px;background:var(--grey-box);border-radius:3px;padding:12px 18px 0 29px}
.quote{position:relative;font-size:11px;line-height:16.3px;color:#444;letter-spacing:.15px}
.quote::before{content:"\201C";position:absolute;left:-22px;top:-6px;font:700 30px Georgia,serif;color:#c5c8cb}
.quote-close{font:700 24px Georgia,serif;color:#c5c8cb;line-height:0;vertical-align:-10px}
.quote-author{font-size:11px;color:#222;margin-top:6px}
.testimonial+.testimonial{border-top:1px solid #d6d9dc;margin-top:10px;padding-top:16px}

/* footer */
.site-footer{left:82px;top:957px;width:876px;height:168px;background:var(--cyan);border-radius:3px;color:#fff}
.footer-col{position:absolute;top:11px}
.footer-col h4{font-family:"Ubuntu",sans-serif;font-weight:400;font-size:14px;margin-bottom:10px;letter-spacing:.2px}
.footer-col ul{list-style:none;font-size:11px;line-height:18px}
.footer-col li::before{content:"";display:inline-block;border-left:4px solid rgba(255,255,255,.6);border-top:3px solid transparent;border-bottom:3px solid transparent;margin:0 9px 0 2px}
.field{background:#fff;border:1px solid #b9e7ee;font-size:11px;color:#999;padding:3px 5px}
.submit-btn{width:67px;height:22px;border-radius:5px;background:linear-gradient(#ff9a3e,var(--orange));border:1px solid #c84f0c;color:#fff;font-weight:700;font-size:12px;text-align:center;line-height:20px}
.pay-badge{width:54px;height:34px;background:#fff;border-radius:3px;box-shadow:0 1px 2px rgba(0,0,0,.25);font-size:10px;font-weight:700;color:#1c5a8c;display:flex;align-items:center;justify-content:center}
.pay-badge.is-dark{background:#1e1e1e;color:#e8e8e8}
.social-strip{width:117px;height:34px;background:#15a9c0;border-radius:3px;display:flex;gap:9px;padding:4px 6px}
.social-strip i{width:28px;height:26px;border-radius:3px;background:#0f8ca0}

.copyright-bar{left:82px;top:1136px;width:876px;height:32px;background:#fff;border:1px solid var(--panel-line);border-radius:3px;font-size:11px;display:flex;justify-content:space-between;align-items:center;padding:0 14px 0 8px}
.copyright-bar nav span{margin:0 9px}
</style>
</head>
<body>

<header>
  <div class="abs logo">
    <div class="logo-mark" role="img" aria-label="Easel with palette emblem"></div>
    <span class="logo-name">THE VELVET EASEL CO</span>
  </div>
  <div class="abs account-links">Login<span>|</span>New User?</div>
  <div class="abs order-cta">Order your painting now<br>in 3 easy steps
    <svg width="14" height="10" viewBox="0 0 14 10"><path d="M0 0h14L6 10z" fill="#d9961a"/></svg>
  </div>
</header>

<nav class="abs main-nav">
  <a class="nav-item is-active" style="margin-right:30px">How It Works</a>
  <a class="nav-item" style="margin-right:30px">Order Your Painting</a>
  <a class="nav-item" style="margin-right:30px">Galleries</a>
  <a class="nav-item" style="margin-right:38px">Gift ideas</a>
  <a class="nav-item" style="margin-right:36px">Testimonials</a>
  <a class="nav-item" style="margin-right:36px">FAQ</a>
  <a class="nav-item" style="margin-right:34px">Prices</a>
  <a class="nav-item" style="margin-right:34px">Guarantee</a>
  <a class="nav-item">Contact us</a>
</nav>

<div class="abs content-panel"></div>

<section>
  <div class="abs slider-frame"></div>
  <div class="abs slide-before" role="img" aria-label="Original portrait photo of a woman with a pearl necklace"></div>
  <div class="abs slide-after" role="img" aria-label="Hand-painted oil portrait made from the photo"></div>
  <div class="abs slide-strip" role="img" aria-label="Slide thumbnails"><i></i><i></i><i></i><i></i><i></i><i></i></div>
  <div class="abs slider-arrow" style="left:92px"><svg width="16" height="14" viewBox="0 0 16 14"><path d="M7 1 1 7l6 6M1 7h14" stroke="#8a8f94" stroke-width="2.4" fill="none"/></svg></div>
  <div class="abs slider-arrow" style="left:905px"><svg width="16" height="14" viewBox="0 0 16 14"><path d="M9 1l6 6-6 6M15 7H1" stroke="#8a8f94" stroke-width="2.4" fill="none"/></svg></div>
</section>

<section>
  <div class="abs thumb-row"></div>
  <div class="abs thumb" style="left:103px;background:linear-gradient(#2a1e1c,#c98a7c 50%,#d8dde6);border-color:#f26a1b" role="img" aria-label="Portrait sample: lips and collar detail"></div>
  <div class="abs thumb" style="left:239px;background:linear-gradient(90deg,#f2f0ee,#7a5a44 40%,#d9b49a 55%,#f2f0ee);border-color:#ee3f6f" role="img" aria-label="Portrait sample: woman with long hair"></div>
  <div class="abs thumb" style="left:382px;background:linear-gradient(#2c2420,#c8804c 45%,#e3aa80);border-color:#1fc5dc" role="img" aria-label="Portrait sample: smiling woman with sunglasses"></div>
  <div class="abs thumb" style="left:526px;background:linear-gradient(100deg,#e8e8e8,#b98c76 40%,#a06e58);border-color:#7cc242" role="img" aria-label="Portrait sample: close-up of an eye"></div>
  <div class="abs thumb" style="left:669px;background:linear-gradient(#d9c9a8,#a08868 55%,#3a302a);border-color:#3a5fb0" role="img" aria-label="Portrait sample: vintage photo of a young boy"></div>
  <div class="abs thumb" style="left:810px;background:linear-gradient(#2a1e1c,#c98a7c 50%,#d8dde6);border-color:#7a2fa6" role="img" aria-label="Portrait sample: lips and collar detail"></div>
</section>

<section>
  <h2 class="abs section-head" style="left:90px;top:583px;width:580px;font-weight:400">LET US PAINT YOUR LIFE!</h2>
  <div class="abs features">
    <div class="feature"><h3>Quality</h3><p>All our artworks are created by hand by experienced professional portrait artists using top quality paints and materials.</p></div>
    <div class="feature" style="margin-top:15px"><h3>Prices - We ask for only 20% advance payment</h3><p>Our prices are affordable - oil portraits on canvas from $99 and charcoal portraits from $69 only!</p></div>
    <div class="feature" style="margin-top:16px"><h3>Design</h3><p>Our portrait painters can combine several photos into 1 portrait painting.</p></div>
    <div class="feature" style="margin-top:24px"><h3>Handpainted</h3><p>Our artworks are hand painted by real painting artists. They are NOT computer generated.</p></div>
    <div class="feature" style="margin-top:15px"><h3>Delivery</h3><p>Our unique express service makes our portraits a great gift idea for anniversary gifts, birthday gifts, photo gifts or any unique gifts.</p></div>
    <div class="feature" style="margin-top:15px"><h3>Variety</h3><p>Our artists can handle creation of beautiful pet portraits, family portraits, self portraits and much more. Visit our Galleries section for more!</p></div>
  </div>
</section>

<aside>
  <h2 class="abs section-head" style="left:699px;top:583px;width:247px;font-weight:400">CLIENT TESTIMONIALS</h2>
  <div class="abs testimonials">
    <div class="testimonial">
      <p class="quote">This painting is a Christmas gift for my mom. My brother is currently serving in Afghanistan and I wanted her to have a special gift this year. I`m so happy with this painting, you captured every detail. Thank you! <span class="quote-close">&#8221;</span></p>
      <p class="quote-author">Client Name</p>
    </div>
    <div class="testimonial">
      <p class="quote">This painting is a Christmas gift for my mom. My brother is currently serving in Afghanistan and I wanted her to have a special gift this year. I`m so happy with this painting, you captured every detail. Thank you! <span class="quote-close">&#8221;</span></p>
      <p class="quote-author">Client Name</p>
    </div>
  </div>
</aside>

<footer class="abs site-footer">
  <div class="footer-col" style="left:8px">
    <h4>ABOUT CANVASLANE ART</h4>
    <ul><li>Portrait painting</li><li>About us</li><li>Partners</li><li>Affiliates</li><li>Photo tips</li><li>Terms &amp; conditions</li></ul>
  </div>
  <div class="footer-col" style="left:217px">
    <h4>OTHER LINKS</h4>
    <ul><li>Articles</li><li>Products</li><li>Photo sur toile</li><li>Portraitmalerei</li><li>Transformar fotos</li><li>Foto su tela</li></ul>
  </div>
  <div class="footer-col" style="left:425px">
    <h4>SAY SOMETHING!</h4>
    <div class="abs field" style="left:1px;top:29px;width:201px;height:20px">Email Address</div>
    <div class="abs field" style="left:1px;top:56px;width:201px;height:64px">Comments</div>
    <div class="abs submit-btn" style="left:0;top:128px">Submit</div>
  </div>
  <div class="footer-col" style="left:740px">
    <h4>PAYMENT OPTIONS</h4>
    <div class="abs pay-badge" style="left:-1px;top:28px">Coinvale</div>
    <div class="abs pay-badge" style="left:63px;top:28px">Cardora</div>
    <div class="abs pay-badge is-dark" style="left:-1px;top:67px">Mastline</div>
    <div class="abs pay-badge is-dark" style="left:63px;top:67px">Wiremark</div>
    <div class="abs social-strip" style="left:-1px;top:109px"><i></i><i></i><i></i></div>
  </div>
</footer>

<div class="abs copyright-bar">
  <span>Copyright © 2007- 2011 Canvaslane Art.</span>
  <nav>Home<span>|</span>About us<span>|</span>Sitemap</nav>
</div>

</body>
</html>
```